Bramble firearms training and consulting

Business card for a new firearms training company. I train persons on firearms safety, personal protection, shooting tactics and CHL.Im a Prior State trooper. I also served 4 years in IRaq as a Protection contractor with the Dept of State. Real world training for Real world situations. I would like the company name to be, BRAMBLE FIREARMS TRAINING AND CONSULTING. Im native american also. Ive provided pics. Put the name Bramble above the arrowhead but rotate the arrowhead to the right with it pointing right. Then place bramble inside the arrowhead. lets see both.
Industry/Entity Type
Business
Contact Information for Business Card
Christian Chatellier817-240-0488shadowtraining33@gmail.com

```html
<!DOCTYPE html>
<html lang="en">
<head>
<meta charset="utf-8">
<title>Bramble Firearms Training and Consulting – Business Card</title>
<link rel="stylesheet" href="https://fonts.googleapis.com/css2?family=Della+Respira&display=swap">
<style>
  :root {
    --stage: #141414;
    --card: #f3f3f1;
    --brand-red: #7d1a0e;
    --ink: #1a1a1a;
    --serif: "Della Respira", Georgia, serif;
    --sans: Arial, Helvetica, sans-serif;
  }
  * { box-sizing: border-box; margin: 0; padding: 0; }
  html, body {
    width: 1200px; height: 1073px; overflow: hidden;
    background: var(--stage);
  }
  .card {
    position: absolute; left: 263px; top: 19px;
    width: 631px; height: 1039px;
    background: var(--card);
    font-family: var(--serif);
    color: var(--ink);
  }
  .band { position: absolute; left: 165px; width: 302px; background: var(--brand-red); }
  .band--top { top: 0; height: 39px; }
  .rule--top { top: 46px; height: 4px; }
  .rule--bottom { top: 985px; height: 4px; }
  .band--bottom { top: 993px; height: 46px; }
  .holder { position: absolute; top: 104px; width: 100%; text-align: center; }
  .holder__name { font-size: 43px; font-weight: 400; letter-spacing: 0.5px; line-height: 1; }
  .holder__role { font-size: 19px; margin-top: 6px; }
  .brand {
    position: absolute; top: 418px; width: 100%; text-align: center;
  }
  .brand__name {
    font-family: var(--serif); font-size: 92px; color: var(--brand-red);
    letter-spacing: 4px; line-height: 1;
  }
  .brand__tagline {
    margin-top: 74px; font-family: var(--sans); font-size: 24px;
    color: var(--brand-red); letter-spacing: 0.3px;
  }
  .contacts {
    position: absolute; top: 834px; width: 100%;
    list-style: none; display: flex; flex-direction: column; align-items: center; gap: 8px;
  }
  .contacts__item { display: flex; align-items: center; gap: 14px; font-size: 29px; line-height: 36px; }
  .contacts__icon { width: 30px; height: 30px; flex: none; }
</style>
</head>
<body>
  <article class="card">
    <div class="band band--top"></div>
    <div class="band rule--top"></div>

    <header class="holder">
      <h1 class="holder__name">Dorian Pellwick</h1>
      <p class="holder__role">Trainer and Consultant</p>
    </header>

    <section class="brand">
      <p class="brand__name">BRAMBLE</p>
      <p class="brand__tagline">FIREARMS TRAINING AND CONSULTING</p>
    </section>

    <ul class="contacts">
      <li class="contacts__item">
        <svg class="contacts__icon" viewBox="0 0 30 30" aria-hidden="true">
          <circle cx="15" cy="15" r="13" fill="none" stroke="#1a1a1a" stroke-width="2"/>
          <path d="M10 8.5c1-.6 2-.4 2.5.5l1.2 2.3c.4.8.1 1.5-.6 2l-.8.6c.8 1.8 2.2 3.2 4 4l.6-.8c.5-.7 1.2-1 2-.6l2.3 1.2c.9.5 1.1 1.5.5 2.5-1 1.6-3 2-5.2.9-3.2-1.6-5.6-4-7.2-7.2C8 11.5 8.4 9.5 10 8.5z" fill="#1a1a1a"/>
        </svg>
        <span>555-317-9062</span>
      </li>
      <li class="contacts__item">
        <svg class="contacts__icon" viewBox="0 0 30 30" aria-hidden="true">
          <circle cx="15" cy="15" r="14" fill="#1a1a1a"/>
          <rect x="8" y="10" width="14" height="10" rx="1" fill="#f3f3f1"/>
          <path d="M8 11l7 5 7-5" fill="none" stroke="#1a1a1a" stroke-width="1.5"/>
        </svg>
        <span>bramblecourse58@mailvento.com</span>
      </li>
      <li class="contacts__item">
        <svg class="contacts__icon" viewBox="0 0 30 30" aria-hidden="true">
          <circle cx="15" cy="15" r="14" fill="#1a1a1a"/>
          <path d="M15 7.5l-8 7h2.2V22h4.3v-4.5h3V22h4.3v-7.5H23z" fill="#f3f3f1"/>
        </svg>
        <span>48 Linden Row, Harlow, NY 12044</span>
      </li>
    </ul>

    <div class="band rule--bottom"></div>
    <div class="band band--bottom"></div>
  </article>
</body>
</html>
```